Newsletter Ad

I am looking for someone to design an advertisement for a mother's club newsletter. 4" wide X by 5" tall (and 2.5" wide X 5" tall if possible).

I'm a psychotherapist, so want the ad to look professional, but modern. I have a logo with my photo attached that can be incorporated into the design. The colors of my website are turquoise and white. I'd like to keep with that theme...so maybe some turquoise blocking to match the logo font color.

I'm uploading a logo as well as an ad draft with the content I'd like listed in the ad.

```html
<!DOCTYPE html>
<html lang="en">
<head>
<meta charset="utf-8">
<title>Dana Wells, MA, MFT – Newsletter Ad</title>
<link href="https://fonts.googleapis.com/css2?family=Questrial&display=swap" rel="stylesheet">
<style>
  :root {
    --white: #ffffff;
    --turquoise: #03cec4;
    --teal-ink: #2a9a94;
    --ink: #1b1b1b;
    --portrait-light: #d9c6b4;
    --portrait-dark: #5a4636;
  }
  * { margin: 0; padding: 0; box-sizing: border-box; }
  html, body {
    width: 961px; height: 1200px; overflow: hidden;
    background: var(--white);
  }
  .ad {
    position: relative;
    width: 961px; height: 1200px;
    background: var(--white);
    font-family: "Questrial", "Century Gothic", sans-serif;
    color: var(--ink);
  }
  .portrait {
    position: absolute; left: 0; top: 0;
    width: 228px; height: 362px;
    background: linear-gradient(160deg, var(--portrait-light) 0%, #a88a70 55%, var(--portrait-dark) 100%);
    border-radius: 0 0 40px 0;
  }
  .header {
    position: absolute; left: 228px; right: 0; top: 0; height: 362px;
    text-align: center;
  }
  .name {
    position: absolute; left: 0; right: 0; top: 86px;
    padding-right: 140px;
    padding-left: 10px;
    font-size: 58px; font-weight: 400; letter-spacing: 1px;
    color: var(--teal-ink); line-height: 1;
  }
  .tagline {
    position: absolute; left: 0; right: 0; top: 212px;
    padding-right: 138px;
    font-size: 32px; line-height: 44px; color: var(--ink);
  }
  .services-band {
    position: absolute; left: 0; top: 362px;
    width: 961px; height: 756px;
    background: var(--turquoise);
  }
  .services {
    list-style: none;
    position: absolute; left: 0; right: 0; top: 48px;
    text-align: center;
    color: var(--white);
    font-size: 39px; line-height: 60.5px;
  }
  .contact {
    position: absolute; left: 0; right: 0; top: 570px;
    text-align: center; color: var(--ink);
    font-style: normal;
  }
  .contact .address { font-size: 30px; line-height: 46px; }
  .contact .line { font-size: 27px; line-height: 40px; display: block; }
  .license {
    position: absolute; right: 32px; top: 1134px;
    font-size: 22px; color: var(--ink);
  }
</style>
</head>
<body>
  <div class="ad">
    <div class="portrait" role="img" aria-label="Portrait photo of the therapist"></div>

    <header class="header">
      <h1 class="name">DANA WELLS, MA, MFT</h1>
      <p class="tagline">Psychotherapy for<br>Individuals, Couples and Families</p>
    </header>

    <section class="services-band">
      <ul class="services">
        <li>Parenting</li>
        <li>Depression</li>
        <li>Anxiety</li>
        <li>Life Transitions</li>
        <li>Divorce</li>
        <li>Couples Issues</li>
        <li>Women’s Issues</li>
        <li>Attachment and Neuroscience</li>
      </ul>

      <address class="contact">
        <span class="line address">418 Harbor Lane, Fairhaven, CA 94000</span>
        <span class="line">www.danawells.com</span>
        <span class="line">dana@danawells.com</span>
        <span class="line">415.555.0148</span>
      </address>
    </section>

    <p class="license">License# MFC48213</p>
  </div>
</body>
</html>
```